High-end construction company needs a business card design

We need a modern looking business card that draws people in, is memorable and looks so good people will want to sick it on their fridges.
On the first side what is needed are:
Logo
My name - Tomasz Brelwik
Title - Managing Director
Website - www.varkelt.co.uk
Email - tomasz@varkelt.co.uk
Telephone - 020 5194 6281
Mobile - 07845139072
On the back side was is needed is a list of all the services we provide:
-Kitchen Renovations
-Bathroom Renovations
-House Renovations
-Garage Conversions
-Extensions
-Loft Conversions
-Conservatories
-Carpentry
-Tiling
-Electrical
-Plumbing & Heating
-Bricklaying
-Landscaping
-Decorating
-Plastering
We would like the colours to be the same shades as on the logo with grey or black for the words.
Target Market(s)
Anyone who needs building work done
Contact Information for Business Card
This business card is for a construction company which strives to deliver excellent service and quality.
The look and feel of the card should represent this.
Requirements
Must have
- On the first side what is needed are:
Logo
My name - Tomasz Brelwik
Title - Managing Director
Website - www.varkelt.co.uk
Email - tomasz@varkelt.co.uk
Telephone - 020 5194 6281
Mobile - 07845139072
Nice to have
- Cool looking features

```html
<!DOCTYPE html>
<html lang="en">
<head>
<meta charset="utf-8">
<title>Varkelt Construction Ltd – Business Card</title>
<link rel="stylesheet" href="https://fonts.googleapis.com/css2?family=Exo+2:wght@400;600;700;800&family=Roboto:wght@300;400&display=swap">
<style>
  :root {
    --green-deep: #3c9a3f;
    --green-mid: #5cb548;
    --green-light: #8cc94f;
    --green-line: #7ec242;
    --paper: #f7f7f5;
    --paper-shade: #e8e9e6;
    --ink: #7a7d7a;
    --ink-dark: #5d605d;
    --white: #ffffff;
    --stage: #e6e8e3;
  }
  * { margin: 0; padding: 0; box-sizing: border-box; }
  html, body {
    width: 1200px; height: 780px; overflow: hidden;
    background: var(--stage);
  }
  .canvas {
    position: relative; width: 1200px; height: 780px;
    display: flex; align-items: center; justify-content: center; gap: 48px;
  }
  .card {
    position: relative; width: 540px; height: 340px;
    border-radius: 18px; overflow: hidden;
    box-shadow: 0 10px 26px rgba(0,0,0,.16), 0 2px 4px rgba(0,0,0,.08);
  }

  /* Front */
  .card--front {
    background: linear-gradient(160deg, var(--white) 30%, var(--paper) 60%, var(--paper-shade) 100%);
  }
  .front-swoosh { position: absolute; inset: 0; width: 100%; height: 100%; }
  .holder {
    position: absolute; top: 14px; right: 30px; text-align: right; color: var(--white);
  }
  .holder__name {
    font-family: "Exo 2", sans-serif; font-weight: 800; font-size: 21px;
    letter-spacing: .5px; text-transform: uppercase; line-height: 1.1;
  }
  .holder__title {
    font-family: "Roboto", sans-serif; font-weight: 400; font-size: 13px; margin-top: 1px;
  }
  .brand {
    position: absolute; left: 222px; top: 146px;
    display: flex; align-items: center; gap: 12px;
  }
  .brand__square { width: 30px; height: 30px; background: var(--green-mid); }
  .brand__name {
    font-family: "Exo 2", sans-serif; font-weight: 700; color: var(--green-mid);
    text-transform: uppercase; line-height: 1.02;
  }
  .brand__name .big { display: block; font-size: 44px; letter-spacing: 1px; }
  .brand__name .small { display: block; font-size: 15px; letter-spacing: 2.4px; }
  .divider {
    position: absolute; left: 118px; right: 34px; top: 248px; height: 1px;
    background: var(--green-line);
  }
  .contacts {
    position: absolute; left: 128px; top: 264px;
    display: flex; align-items: stretch; gap: 22px;
    font-family: "Roboto", sans-serif; font-weight: 300; color: var(--ink); font-size: 15px;
  }
  .contacts__group { display: flex; flex-direction: column; gap: 6px; }
  .contacts__group--small { font-size: 13px; padding-top: 2px; }
  .contacts__rule { width: 1px; background: var(--ink); opacity: .6; }
  .contact { display: flex; align-items: center; gap: 8px; white-space: nowrap; }
  .contact__icon { width: 15px; height: 15px; flex: none; }

  /* Back */
  .card--back {
    background: linear-gradient(200deg, var(--green-light) 0%, var(--green-mid) 50%, var(--green-deep) 100%);
    color: var(--white);
  }
  .services { position: absolute; left: 34px; right: 24px; top: 44px; }
  .services__heading {
    font-family: "Exo 2", sans-serif; font-weight: 800; font-size: 22px;
    text-transform: uppercase; letter-spacing: .5px; margin-left: 190px; margin-bottom: 16px;
  }
  .services__list {
    list-style: none; font-family: "Roboto", sans-serif; font-weight: 400; font-size: 14.5px;
    line-height: 1.75;
  }
  .services__list li { white-space: nowrap; }
  .services__web {
    position: absolute; left: 40px; bottom: 52px;
    font-family: "Roboto", sans-serif; font-weight: 300; font-size: 14px; letter-spacing: 6px;
  }
</style>
</head>
<body>
<main class="canvas">

  <section class="card card--front" aria-label="Front of business card">
    <svg class="front-swoosh" viewBox="0 0 540 340" preserveAspectRatio="none" aria-hidden="true">
      <defs>
        <linearGradient id="bandGreen" x1="0" y1="1" x2="1" y2="0">
          <stop offset="0" stop-color="#3c9a3f"/>
          <stop offset="1" stop-color="#5fb84b"/>
        </linearGradient>
      </defs>
      <path d="M0 0 H540 V50 C 300 52, 60 150, 24 340 H0 Z" fill="url(#bandGreen)"/>
      <path d="M540 64 C 310 66, 80 160, 44 340" fill="none" stroke="#8cc94f" stroke-width="6"/>
    </svg>

    <div class="holder">
      <p class="holder__name">Tomasz Brelwik</p>
      <p class="holder__title">Managing Director</p>
    </div>

    <div class="brand">
      <span class="brand__square" aria-hidden="true"></span>
      <p class="brand__name"><span class="big">Varkelt</span><span class="small">Construction Ltd</span></p>
    </div>

    <div class="divider"></div>

    <div class="contacts">
      <div class="contacts__group">
        <p class="contact">
          <svg class="contact__icon" viewBox="0 0 16 16" aria-hidden="true"><circle cx="8" cy="8" r="8" fill="#7ec242"/><path d="M5.2 4.2l1.4-.3.8 2-1 .8c.5 1.1 1.3 1.9 2.4 2.4l.8-1 2 .8-.3 1.4c-3.4.1-6.2-2.7-6.1-6.1z" fill="#fff"/></svg>
          020 5194 6281
        </p>
        <p class="contact">
          <svg class="contact__icon" viewBox="0 0 16 16" aria-hidden="true"><circle cx="8" cy="8" r="8" fill="#7ec242"/><rect x="5.3" y="3.3" width="5.4" height="9.4" rx="1" fill="#fff"/><rect x="6.2" y="4.5" width="3.6" height="6" fill="#7ec242"/></svg>
          07845139072
        </p>
      </div>
      <span class="contacts__rule" aria-hidden="true"></span>
      <div class="contacts__group contacts__group--small">
        <p class="contact">
          <svg class="contact__icon" viewBox="0 0 16 16" aria-hidden="true"><circle cx="8" cy="8" r="8" fill="#7ec242"/><rect x="4" y="5" width="8" height="6" rx=".8" fill="#fff"/><path d="M4.3 5.4L8 8.3l3.7-2.9" fill="none" stroke="#7ec242" stroke-width=".9"/></svg>
          tomasz@varkelt.co.uk
        </p>
        <p class="contact">
          <svg class="contact__icon" viewBox="0 0 16 16" aria-hidden="true"><circle cx="8" cy="8" r="8" fill="#7ec242"/><circle cx="8" cy="8" r="4" fill="none" stroke="#fff" stroke-width="1"/><path d="M4 8h8M8 4c-1.6 2.4-1.6 5.6 0 8M8 4c1.6 2.4 1.6 5.6 0 8" fill="none" stroke="#fff" stroke-width=".8"/></svg>
          www.varkelt.co.uk
        </p>
      </div>
    </div>
  </section>

  <section class="card card--back" aria-label="Back of business card">
    <div class="services">
      <h2 class="services__heading">Our Services</h2>
      <ul class="services__list">
        <li>Kitchen Renovations | Bathroom Renovations | House Renovations</li>
        <li>Garage Conversions | Extensions | Loft Conversions | Conservatories</li>
        <li>Carpentry | Tiling | Electrical | Plumbing &amp; Heating | Bricklaying</li>
        <li>Landscaping | Decorating | Plastering</li>
      </ul>
    </div>
    <p class="services__web">www.varkelt.co.uk</p>
  </section>

</main>
</body>
</html>
```